Kestrelford Therapy and Consulting

Build & publish a WordPress website that advertises and markets my private practice - which is delivering, and consulting in, psychological therapies. I also need to be able to edit content (eg text and images) on the end product thereafter. It should have a call to action on the homepage, links to:
• About me
• For referrers (with link to service fees)
• Contact details – phone#, email address, location, operating hours, and service fees
• Other resources

Target Market(s)

People struggling with mental health, relationships, and/or psychological disorders

Industry/Entity Type

Mental health

Coding

Coded - Design and coding required

Number of Pages Required

4 page

Requirements
Must have
• WordPress
Nice to have
• Please make my logo standout on the home page
Should not have
• No testimonials - they're forbidden for psychologists in Australia

```html
<!DOCTYPE html>
<html lang="en">
<head>
<meta charset="utf-8">
<title>Kestrelford Therapy and Consulting</title>
<link href="https://fonts.googleapis.com/css2?family=Cormorant+Garamond:wght@500;600;700&family=Roboto:wght@300;400;500&display=swap" rel="stylesheet">
<style>
:root{
  --pink:#d793dc;
  --pink-deep:#c97fd0;
  --cyan:#4fcfe4;
  --ink:#2b2b2b;
  --text:#3a3a3a;
  --muted:#6a6a6a;
  --white:#ffffff;
  --black:#000000;
  --serif:'Cormorant Garamond', Georgia, serif;
  --sans:'Roboto', Arial, sans-serif;
}
*{margin:0;padding:0;box-sizing:border-box}
html,body{width:1200px;height:5141px;overflow:hidden}
body{background:var(--white);font-family:var(--sans);color:var(--text)}
.page{position:relative;width:1200px;height:5141px;overflow:hidden}
.abs{position:absolute}

/* nav */
.site-header{position:absolute;left:0;top:0;width:1200px;height:74px;background:var(--white);z-index:3}
.brand{position:absolute;left:110px;top:18px;display:flex;align-items:center;gap:10px}
.brand-mark{width:40px;height:40px;border-radius:50%;background:#9fb7d6}
.brand-name{font-family:var(--serif);font-weight:600;color:#5a6a7a;line-height:1}
.brand-name .main{display:block;font-size:24px}
.brand-name .sub{display:block;font-size:9px;letter-spacing:1.5px;text-transform:uppercase;margin-top:3px}
.main-nav{position:absolute;top:28px;left:0;width:1200px;font-size:14px;color:#444}
.main-nav a{position:absolute;color:inherit;text-decoration:none;white-space:nowrap}
.main-nav a.current{color:var(--pink)}
.btn{display:inline-block;background:var(--pink);color:var(--white);border-radius:20px;font-size:14px;text-align:center;text-decoration:none}
.nav-cta{position:absolute;left:968px;top:17px;width:96px;height:38px;line-height:38px}

/* hero */
.hero{position:absolute;left:0;top:74px;width:1200px;height:680px}
.hero svg{position:absolute;left:0;top:0}
.hero-copy{position:absolute;left:112px;top:156px;color:var(--white)}
.hero-copy .welcome{font-weight:300;font-size:30px}
.hero-copy h1{font-family:var(--serif);font-weight:700;font-size:92px;line-height:.95;margin-top:2px}
.hero-copy .tagline{font-weight:300;font-size:26px;margin-top:2px}
.hero-copy p{font-size:13px;line-height:24px;width:430px;margin-top:4px}

/* common */
.section-title{font-family:var(--serif);font-weight:500;font-size:34px;color:var(--ink);line-height:1}
.section-title .initial{color:var(--pink);font-size:42px}
.body-copy{font-size:13px;line-height:28px;color:var(--text)}
.photo{background:linear-gradient(135deg,#9aa1a0,#d8d3cb)}

/* about */
.about-photo{left:140px;top:826px;width:388px;height:412px;border-radius:16px;background:linear-gradient(160deg,#4f6b3c,#8a9a72 55%,#5a4e40)}
.about-copy{left:588px;top:826px;width:510px}
.about-copy .who{font-family:var(--sans);font-size:18px;color:var(--muted);font-weight:300}
.about-copy .role{font-size:13px;line-height:22px;margin-top:14px;color:#555}
.about-copy .body-copy{margin-top:18px}
.credentials{list-style:none;margin-top:12px}
.credentials li{display:flex;align-items:center;gap:8px;font-size:13px;height:43px}
.credentials svg{flex:none}

/* services oval */
.services-oval{left:0;top:1300px;width:1200px;height:560px}
.services-head{left:0;top:1352px;width:1200px;text-align:center}
.services-head p{font-size:14px;line-height:22px;margin-top:10px;color:#1f3a40}
.service{width:200px;text-align:center}
.service .disc{width:194px;height:194px;border-radius:50%;margin:0 auto}
.service .label{font-size:19px;color:#11343a;margin-top:14px}
.slider-arrow{width:28px;height:28px;border-radius:50%}

/* interests */
.interests-title{left:0;top:1926px;width:1200px;text-align:center}
.interest{width:200px;text-align:center}
.interest .icon{width:80px;height:80px;border-radius:50%;margin:0 auto;background:#f3dcf5}
.interest .label{font-family:var(--serif);font-weight:600;font-size:20px;color:var(--ink);margin-top:14px}
.view-more{left:540px;top:2126px;width:120px;height:38px;line-height:38px}

/* feature rows */
.feature-photo{border-radius:0 14px 14px 0}
.feature-copy .body-copy{margin-top:18px}

/* bottom oval */
.info-oval{left:0;top:3790px;width:1200px;height:480px}
.info-disc{width:232px;height:232px;border-radius:50%;color:var(--white);display:flex;flex-direction:column;align-items:center;justify-content:flex-end;text-align:center;padding-bottom:48px}
.info-disc .label{font-size:20px}
.info-disc.parking{justify-content:center;padding:0 30px}
.info-disc.parking .label{font-size:19px;line-height:24px}
.info-disc.parking p{font-size:11px;line-height:23px;margin-top:8px}

/* referrers */
.referrers{left:0;top:4350px;width:1200px;text-align:center}
.referrers .body-copy{width:750px;margin:22px auto 0}
.service-fees{left:544px;top:4608px;width:112px;height:36px;line-height:36px}

/* footer */
.site-footer{left:0;top:4740px;width:1200px;height:401px;color:var(--white)}
.footer-brand{left:0;top:4834px;width:1200px;display:flex;justify-content:center;align-items:center;gap:10px}
.footer-brand .brand-name{color:var(--white)}
.footer-brand .brand-mark{background:var(--white)}
.footer-nav{left:0;top:4902px;width:1200px;font-size:13px;color:var(--white)}
.footer-nav a{position:absolute;color:inherit;text-decoration:none;white-space:nowrap}
.contact-item{width:260px;text-align:center;font-size:13px;line-height:20px;color:var(--white)}
.contact-item .ring{width:46px;height:46px;border-radius:50%;border:2px solid var(--white);margin:0 auto 14px;display:flex;align-items:center;justify-content:center}
.copyright{left:0;top:5102px;width:1200px;text-align:center;font-size:11px;color:var(--white)}
</style>
</head>
<body>
<div class="page">

  <header class="site-header">
    <div class="brand">
      <span class="brand-mark"></span>
      <span class="brand-name"><span class="main">Kestrelford</span><span class="sub">Therapy and Consulting</span></span>
    </div>
    <nav class="main-nav">
      <a class="current" style="left:352px">Home</a>
      <a style="left:449px">About Us</a>
      <a style="left:565px">Services</a>
      <a style="left:674px">For Referrers</a>
      <a style="left:815px">Other Resources</a>
    </nav>
    <a class="btn nav-cta">Contact Us</a>
  </header>

  <section class="hero">
    <svg width="1200" height="680" viewBox="0 0 1200 680">
      <defs>
        <linearGradient id="heroTone" x1="0" y1="0" x2="1" y2="0">
          <stop offset="0" stop-color="#3f3f3f"/>
          <stop offset=".55" stop-color="#7c7c7c"/>
          <stop offset="1" stop-color="#c8c8c8"/>
        </linearGradient>
        <clipPath id="heroClip"><path d="M0,0 H1200 V481 Q600,806 0,481 Z"/></clipPath>
      </defs>
      <rect role="img" aria-label="Therapist in session with a young client in a calm consulting room" width="1200" height="680" fill="url(#heroTone)" clip-path="url(#heroClip)"/>
      <path d="M0,481 Q600,806 1200,481 L1200,493 Q600,855 0,493 Z" fill="var(--pink)"/>
    </svg>
    <div class="hero-copy">
      <div class="welcome">Welcome To</div>
      <h1>Kestrelford</h1>
      <div class="tagline">Therapy And Consulting</div>
      <p>Lorem ipsum dolor sit amet, consectetur adipiscing elit, sed do eiusmod tempor incididunt ut labore aliqua.</p>
    </div>
  </section>

  <section class="about">
    <div class="abs about-photo" role="img" aria-label="Portrait of the clinical psychologist"></div>
    <div class="abs about-copy">
      <h2 class="section-title"><span class="initial">A</span>bout <span class="initial">U</span>s <span class="who">Mr Daniel Hartley</span></h2>
      <p class="role">Clinical Psychologist, Clinical Supervisor Kestrelford<br>Therapy and Consulting<br>QUALIFICATIONS:BAppSc(Hons), MPsych(Clin)</p>
      <p class="body-copy">I'm a clinical psychologist, psychotherapist, EMDR Consultant, and Resource Therapy Practitioner and Trainer. My main interest in therapy is helping people overcome the inner obstacles that cause them emotional pain and suffering, and that maintain behavioural patterns that are damaging or self-defeating. I also like to train, coach and mentor other therapists in effective therapies.</p>
      <ul class="credentials">
        <li><svg width="18" height="18" viewBox="0 0 18 18"><circle cx="9" cy="9" r="7.5" fill="none" stroke="#333" stroke-width="1.5"/><path d="M5 9 l3 3 l7 -8" fill="none" stroke="#333" stroke-width="2"/></svg>Allied Psychology Society</li>
        <li><svg width="18" height="18" viewBox="0 0 18 18"><circle cx="9" cy="9" r="7.5" fill="none" stroke="#333" stroke-width="1.5"/><path d="M5 9 l3 3 l7 -8" fill="none" stroke="#333" stroke-width="2"/></svg>Trauma Reprocessing Association (Accredited Practitioner &amp; Consultant)</li>
        <li><svg width="18" height="18" viewBox="0 0 18 18"><circle cx="9" cy="9" r="7.5" fill="none" stroke="#333" stroke-width="1.5"/><path d="M5 9 l3 3 l7 -8" fill="none" stroke="#333" stroke-width="2"/></svg>Inner States Therapy Network (Clinical Resource Therapist &amp; Trainer</li>
      </ul>
    </div>
  </section>

  <section class="services">
    <svg class="abs services-oval" viewBox="0 0 1200 560">
      <ellipse cx="600" cy="282" rx="662" ry="272" fill="var(--pink)"/>
      <ellipse cx="600" cy="276" rx="650" ry="252" fill="var(--cyan)"/>
    </svg>
    <div class="abs services-head">
      <h2 class="section-title">Our Services</h2>
      <p>I provide trauma-focused psychotherapy to clients and consult with other mental<br>health clinicians on their practice of psychotherapy.</p>
    </div>
    <svg class="abs slider-arrow" style="left:48px;top:1580px" viewBox="0 0 28 28"><circle cx="14" cy="14" r="14" fill="#8fc9d3"/><path d="M16 8 l-6 6 l6 6" fill="none" stroke="#fff" stroke-width="2"/></svg>
    <svg class="abs slider-arrow" style="left:1114px;top:1580px" viewBox="0 0 28 28"><circle cx="14" cy="14" r="14" fill="#111"/><path d="M12 8 l6 6 l-6 6" fill="none" stroke="#fff" stroke-width="2"/></svg>
    <div class="abs service" style="left:110px;top:1494px"><div class="disc" role="img" aria-label="Psychotherapy session on a sofa" style="background:linear-gradient(135deg,#c9c3bb,#8e8a86)"></div><div class="label">Psychotherapy</div></div>
    <div class="abs service" style="left:365px;top:1494px"><div class="disc" role="img" aria-label="Clinician completing an assessment" style="background:linear-gradient(135deg,#e4e6e8,#5a5f66)"></div><div class="label">Assessment</div></div>
    <div class="abs service" style="left:630px;top:1494px"><div class="disc" role="img" aria-label="Group professional training workshop" style="background:linear-gradient(135deg,#e8ddd3,#7b5a48)"></div><div class="label">Professional Training</div></div>
    <div class="abs service" style="left:890px;top:1494px"><div class="disc" role="img" aria-label="Clinical supervision conversation" style="background:linear-gradient(135deg,#d9d6cf,#8c8274)"></div><div class="label">Clinical Supervision</div></div>
  </section>

  <section class="interests">
    <h2 class="abs section-title interests-title"><span class="initial">A</span>reas <span class="initial">O</span>f <span class="initial">S</span>pecial <span class="initial">I</span>nterest</h2>
    <div class="abs interest" style="left:90px;top:1990px"><div class="icon" role="img" aria-label="Line illustration for addiction"></div><div class="label">Addiction</div></div>
    <div class="abs interest" style="left:315px;top:1990px"><div class="icon" role="img" aria-label="Line illustration for anger related issues"></div><div class="label">Anger Related Issues</div></div>
    <div class="abs interest" style="left:518px;top:1990px"><div class="icon" role="img" aria-label="Line illustration for anxiety"></div><div class="label">Anxiety</div></div>
    <div class="abs interest" style="left:690px;top:1990px"><div class="icon" role="img" aria-label="Line illustration for panic attacks"></div><div class="label">Panic Attacks</div></div>
    <div class="abs interest" style="left:885px;top:1990px"><div class="icon" role="img" aria-label="Line illustration for assertiveness"></div><div class="label">Assertiveness</div></div>
    <a class="abs btn view-more">View More</a>
  </section>

  <section class="approach">
    <div class="abs photo feature-photo" role="img" aria-label="Therapist talking with two clients" style="left:0;top:2252px;width:490px;height:428px;background:linear-gradient(135deg,#b7a693,#e6e1d8 55%,#8c9a6e)"></div>
    <div class="abs feature-copy" style="left:556px;top:2282px;width:530px">
      <h2 class="section-title"><span class="initial">A</span>pproch / <span class="initial">M</span>odalities</h2>
      <p class="body-copy">EMDR, Existential, Integrative, Mindfulness, Person Centred, Psychodynamic, Schema Therapy, CBT</p>
      <p class="body-copy">I believe that using Eye Movement Desensitizing and Reprocessing (EMDR) therapy and Resource Therapy (RT) together addresses almost all mental illness that doesn't involve an organic component.<br>EMDR principally addresses disturbing memories from the past that negatively impact a person in the present. RT addresses resource states (also known as states of mind, parts, ego states, and schema modes) that are putting a person 'out of balance', i.e. they are yielding unwanted emotions or unwanted behaviours that are impairing a person's ability to function.</p>
    </div>
  </section>

  <section class="quality">
    <div class="abs feature-copy" style="left:112px;top:2896px;width:540px">
      <h2 class="section-title"><span class="initial">Q</span>uality <span class="initial">P</span>rovision</h2>
      <p class="body-copy">I generally start sessions checking with how clients are feeling and coping between sessions, ascertaining whether or not the client believes we are "on track" according to what was agreed in the treatment plan we co-created. I endeavour to maximise the benefit we can obtain from the number of sessions available to us.</p>
    </div>
    <div class="abs photo" role="img" aria-label="Older adults seated in a group session" style="left:714px;top:2770px;width:486px;height:426px;border-radius:14px 0 0 14px;background:linear-gradient(135deg,#d9cbb4,#9fb3bd 55%,#c9c2b6)"></div>
  </section>

  <section class="background">
    <div class="abs photo feature-photo" role="img" aria-label="Two people joining an online video consultation" style="left:0;top:3286px;width:494px;height:428px;background:linear-gradient(135deg,#c7d2d6,#eef0ef 55%,#d6c7b5)"></div>
    <div class="abs feature-copy" style="left:556px;top:3352px;width:530px">
      <h2 class="section-title"><span class="initial">B</span>ackground</h2>
      <p class="body-copy">When I first started to practice, I felt ill-prepared for the vast range of maladies of the human condition, especially as I was immersed in a setting that had so many suffering from the impact of trauma in childhood. Thus, I embarked on decade long learning plan that got me where I am now –equipped with the therapies my practice-based evidence tells me I need, and that satisfies the need for evidence-based practice. I am now substantially trained in EMDR and Resource Therapies, such that I can effectively treat adult survivors of childhood trauma, and supervise or coach others in trauma focused therapies that are effective alone, or in combination.</p>
    </div>
  </section>

  <section class="practice-info">
    <svg class="abs info-oval" viewBox="0 0 1200 480">
      <ellipse cx="600" cy="242" rx="662" ry="232" fill="var(--pink)"/>
      <ellipse cx="600" cy="236" rx="650" ry="214" fill="var(--cyan)"/>
    </svg>
    <div class="abs info-disc" role="img" aria-label="Calendar page for booking appointments" style="left:110px;top:3912px;background:linear-gradient(160deg,#4b5a6a,#1f2a33)"><span class="label">Appointments</span></div>
    <div class="abs info-disc parking" style="left:362px;top:3912px;background:#1d2b3a"><span class="label">Transport And<br>Parking</span><p>There is limited paid parking in Marlow Street and surrounds but, being adjacent to the GPO, Aldgate House is very close to public transport.</p></div>
    <div class="abs info-disc" role="img" aria-label="Wooden blocks spelling fees" style="left:612px;top:3912px;background:linear-gradient(160deg,#7a6a5e,#3f342d)"><span class="label">Fees</span></div>
    <div class="abs info-disc" role="img" aria-label="Paper note about payment options" style="left:866px;top:3912px;background:linear-gradient(160deg,#dcdcdc,#9a9a9a)"><span class="label">payment Options</span></div>
  </section>

  <section class="abs referrers">
    <h2 class="section-title"><span class="initial">F</span>or <span class="initial">R</span>eferrers</h2>
    <p class="body-copy">Lorem ipsum dolor sit amet, consectetur adipiscing elit, sed do eiusmod tempor incididunt ut labore et dolore magna aliqua. Quis ipsum suspendisse ultrices gravida. Risus commodo viverra maecenas accumsan lacus vel facilisis. Lorem ipsum dolor sit amet, consectetur adipiscing elit, sed do eiusmod tempor incididunt ut labore et dolore magna aliqua. Quis ipsum suspendisse ultrices gravida. Risus commodo viverra maecenas accumsan lacus vel facilisis. Lorem ipsum dolor sit amet, consectetur adipiscing elit, sed do eiusmod tempor incididunt ut labore et dolore magna aliqua. Quis ipsum suspendisse ultrices gravida. Risus commodo viverra maecenas accumsan lacus vel facilisis.</p>
  </section>
  <a class="abs btn service-fees">Service Fees</a>

  <footer>
    <svg class="abs site-footer" viewBox="0 0 1200 401">
      <path d="M0,150 Q600,-80 1200,150 V401 H0 Z" fill="var(--pink)"/>
      <path d="M0,165 Q600,-50 1200,165 V401 H0 Z" fill="var(--black)"/>
    </svg>
    <div class="abs footer-brand">
      <span class="brand-mark" style="width:34px;height:34px"></span>
      <span class="brand-name"><span class="main">Kestrelford</span><span class="sub">Therapy and Consulting</span></span>
    </div>
    <nav class="abs footer-nav">
      <a style="left:318px">Home</a>
      <a style="left:413px">About Us</a>
      <a style="left:529px">Services</a>
      <a style="left:638px">For Referrers</a>
      <a style="left:780px">Other Resources</a>
    </nav>
    <div class="abs contact-item" style="left:222px;top:4952px">
      <div class="ring"><svg width="20" height="22" viewBox="0 0 20 22"><path d="M10 1 C5 1 2 4.5 2 8.5 C2 14 10 21 10 21 C10 21 18 14 18 8.5 C18 4.5 15 1 10 1 Z" fill="#fff"/><circle cx="10" cy="8.5" r="3" fill="#000"/></svg></div>
      Suite 4, Aldgate House, 18<br>Marlow Street, Kestrelford,<br>TAS 7000
    </div>
    <div class="abs contact-item" style="left:510px;top:4952px">
      <div class="ring"><svg width="22" height="22" viewBox="0 0 22 22"><circle cx="11" cy="11" r="10" fill="#fff"/><rect x="5.5" y="7" width="11" height="8" fill="#000"/><path d="M5.5 7 l5.5 4.5 l5.5 -4.5" fill="none" stroke="#fff" stroke-width="1.2"/></svg></div>
      info@kestrelford.com
    </div>
    <div class="abs contact-item" style="left:762px;top:4952px">
      <div class="ring"><svg width="20" height="20" viewBox="0 0 20 20"><path d="M4 2 l4 1 l1 4 l-2 1.5 c1 2.5 3 4.5 5.5 5.5 l1.5 -2 l4 1 l1 4 c-1 1.5 -3 2 -5 1.5 c-5 -1.5 -9 -5.5 -10.5 -10.5 c-0.5 -2 0 -4 1.5 -5 z" fill="#fff"/></svg></div>
      <span style="display:block;margin-top:6px">0400 555 018</span>
    </div>
    <p class="abs copyright">Copyright © 2024 Kestrelford Therapy And Consulting | All Rights Reserved</p>
  </footer>

</div>
</body>
</html>
```